Teeth Whitening Clinic Website Redesign - Social Proof Theme

NEW TEETH SITEREVAMP CURRENT WEBSITE:WWW.SANDIEGOSTEETHWHITENING.COMTHEME:SOCIAL PROOF/5 STAR REVIEWS/TESTIMONIALS THEME:https://maps.example.net/QxRvPLoKzN84 I want a testimonial themed, social proof themed website so customers will be sold by testimonials all over the website….I like a nice clean simple site but with all important factors standing out like CALLS TO ACTIONS, for example the $99 special link in header on original design. Also, testimonials throughout the website placed methodically as not to be FORCED and CLUTTEREDKeep all same exact content for all pages and elements of current design. All buttons, calls to action, navigation, etc. Please do not leave anything out from current design. SPECIAL INSTRUCTIONS for banner image:I want to use actual customer photos inside the banner image in a way that really pops and grabs attention. Please grab some customer photos from my PG Account, fk or rateway account: Also, I want to integrate 5 star rateway logo, friendbook review 5 stars icon, searchly business page 5 stars icon, etc. on the banner as well to show social proof as much as possible. Actual customer photos to be used throughout website:https://www.photogram.example/brightharborsmilestudioplace/ https://www.friendbook.com/SDTeethWhitening/https://www.reviewhub.example/biz/bright-harbor-smile-studio-place-bright-harbor-5 Reviews:https://www.reviewhub.example/biz/bright-harbor-smile-studio-place-bright-harbor-5 https://www.friendbook.com/pg/SDTeethWhitening/reviews/?ref=page_internalhttps://goo.gl/maps/TmJcABLAJwC2 Please do home page first to come up with theme then after approval home page we can move forward additional pages.

Target Market(s)

PEOPLE THAT CARE ABOUT DENTAL HYGEINE AND OR CARE ABOUT THEIR TEETH SMILE

Industry/Entity Type

Dental Clinic

Number of Pages Required

5+ page

Colors

Designer to choose colors to be used in the design.

Requirements
Must have
• NEW TEETH SITE
• REVAMP CURRENT WEBSITE:
• WWW.BRIGHTHARBORSMILESTUDIO.EXAMPLE
• THEME:
• SOCIAL PROOF/5 STAR REVIEWS/TESTIMONIALS THEME:
• https://maps.example.net/QxRvPLoKzN84
• I want a testimonial themed, social proof themed website so customers will be sold by testimonials all over the website….I like a nice clean simple site but with all important factors standing out like CALLS TO ACTIONS, for example the $99 special link in header on original design. Also, testimonials throughout the website placed methodically as not to be FORCED and CLUTTERED
• Keep all same exact content for all pages and elements of current design. All buttons, calls to action, navigation, etc. Please do not leave anything out from current design.
• SPECIAL INSTRUCTIONS for banner image:
• I want to use actual customer photos inside the banner image in a way that really pops and grabs attention. Please grab some customer photos from my PG Account, fk or rateway account:
• Also, I want to integrate 5 star rateway logo, friendbook review 5 stars icon, searchly business page 5 stars icon, etc. on the banner as well to show social proof as much as possible.
• Actual customer photos to be used throughout website:
• https://www.photogram.example/brightharborsmilestudioplace/
• https://www.friendbook.example/BHSmileStudio/
• https://www.reviewhub.example/biz/bright-harbor-smile-studio-place-bright-harbor-5
• Reviews:
• https://www.friendbook.example/pg/BHSmileStudio/reviews/?ref=page_internal
• Please do home page first to come up with theme then after approval home page we can move forward additional pages.
Nice to have
• NEW TEETH SITE
• REVAMP CURRENT WEBSITE:
• THEME:
• Reviews:
Should not have
• NEW TEETH SITE
• REVAMP CURRENT WEBSITE:
• THEME:
• Reviews:

```html
<!DOCTYPE html>
<html lang="en">
<head>
<meta charset="utf-8">
<title>Bright Harbor Smile Studio – Home</title>
<link rel="stylesheet" href="https://fonts.googleapis.com/css2?family=Cinzel:wght@700&family=Lato:ital,wght@0,400;0,700;1,400&display=swap">
<style>
:root{
  --blue:#0b9bc7;
  --blue-deep:#0a86ad;
  --blue-row:#0b8db6;
  --ink:#2e2e2e;
  --text:#555;
  --grey-bg:#efefef;
  --foot-bg:#ebebeb;
  --white:#fff;
}
*{margin:0;padding:0;box-sizing:border-box}
html,body{width:1200px;height:3543px;overflow:hidden}
body{font-family:'Lato',sans-serif;color:var(--text);background:var(--white);position:relative}

/* top bar */
.topbar{position:absolute;left:0;top:0;width:1200px;height:52px;background:var(--blue);color:var(--white);font-size:14px}
.topbar .info{position:absolute;top:17px;display:flex;align-items:center;gap:10px}
.topbar .social{position:absolute;left:775px;top:16px;display:flex;gap:22px;font-weight:700;font-size:14px}
.topbar .book{position:absolute;left:914px;top:0;width:274px;height:52px;background:var(--ink);color:var(--white);font-weight:700;font-size:17px;display:flex;align-items:center;justify-content:center;letter-spacing:.5px;border-radius:0 0 6px 6px}

/* header */
.header{position:absolute;left:0;top:52px;width:1200px;height:94px;background:var(--white)}
.brand{position:absolute;left:78px;top:16px;display:flex;align-items:center;gap:12px}
.brand .dot{width:58px;height:58px;border-radius:50%;border:3px solid #c8ced3;background:#f3f6f8}
.brand .name{font-family:'Cinzel',serif;font-weight:700;color:var(--blue);font-size:19px;line-height:22px}
.hinfo{position:absolute;top:20px;display:flex;gap:14px;align-items:center;font-size:14px;color:#555;line-height:21px}
.hinfo .ic{width:52px;height:52px;border-radius:50%;background:#dfe3e6;display:flex;align-items:center;justify-content:center}
.hinfo .ic span{width:34px;height:34px;border-radius:50%;background:var(--blue);display:flex;align-items:center;justify-content:center}

/* nav */
.nav{position:absolute;left:0;top:146px;width:1200px;height:52px;background:var(--ink)}
.nav ul{list-style:none;display:flex;gap:25px;position:absolute;left:78px;top:17px;font-size:15px;color:var(--white);text-transform:uppercase}
.nav li.active{color:var(--blue)}
.nav .call{position:absolute;left:1068px;top:0;width:56px;height:52px;background:var(--blue);display:flex;align-items:center;justify-content:center}

/* hero */
.hero{position:absolute;left:0;top:198px;width:1200px;height:489px;background:var(--blue);overflow:hidden}
.hero h1{position:absolute;left:78px;top:128px;font-family:'Cinzel',serif;font-weight:700;color:var(--white);font-size:40px;line-height:46px;letter-spacing:.5px}
.hero p{position:absolute;left:78px;top:232px;width:470px;color:var(--white);font-size:15px;line-height:26px}
.btn{position:absolute;height:47px;border-radius:24px;font-weight:700;font-size:18px;display:flex;align-items:center;justify-content:center;letter-spacing:.5px}
.btn.solid{background:var(--white);color:var(--blue)}
.btn.ghost{border:2px solid var(--white);color:var(--white)}
.tile{position:absolute;width:130px;height:118px;background:linear-gradient(160deg,#e9e6ea 0%,#6b4b7a 55%,#3a3340 100%)}

/* about */
.about{position:absolute;left:0;top:687px;width:1200px;height:470px;background:var(--white)}
.video-frame{position:absolute;left:78px;top:81px;width:446px;height:200px;border:12px solid var(--ink)}
.video{position:absolute;left:109px;top:114px;width:453px;height:205px;background:linear-gradient(180deg,#f2f2f2,#c9d3da)}
.video .bar{position:absolute;left:0;top:0;width:100%;height:40px;background:linear-gradient(180deg,rgba(0,0,0,.6),rgba(0,0,0,0))}
.about h2{position:absolute;left:650px;top:88px;width:470px;font-family:'Cinzel',serif;font-weight:700;color:var(--blue);font-size:35px;line-height:44px}
.about .lead{position:absolute;left:650px;top:193px;font-style:italic;color:var(--ink);font-size:21px}
.about .body{position:absolute;left:650px;top:231px;width:470px;font-size:13.5px;line-height:22px;color:#666}

/* how */
.how{position:absolute;left:0;top:1157px;width:1200px;height:449px;background:var(--grey-bg);text-align:center}
.section-title{font-family:'Cinzel',serif;font-weight:700;color:var(--blue);font-size:35px;letter-spacing:.5px}
.how h2{position:absolute;left:0;width:1200px;top:46px}
.how .copy{position:absolute;left:182px;top:95px;width:836px;font-size:13.5px;line-height:23.5px;color:#666}
.how .copy p+p{margin-top:18px}

/* why */
.why{position:absolute;left:0;top:1606px;width:1200px;height:728px;background:var(--white)}
.why h2{position:absolute;left:0;width:1200px;text-align:center;top:42px}
.card{position:absolute;width:241px;height:238px;background:var(--white);box-shadow:0 2px 12px rgba(0,0,0,.16);text-align:center;color:#666;font-size:16px;text-transform:uppercase}
.card svg{position:absolute;left:85px;top:62px}
.card span{position:absolute;left:0;width:100%;top:154px}
.card.featured{background:var(--blue);color:var(--white)}

/* compare */
.compare{position:absolute;left:0;top:2334px;width:1200px;height:519px;background:var(--blue)}
.compare h2{position:absolute;left:0;width:1200px;text-align:center;top:50px;color:var(--white)}
.col{position:absolute;top:125px;width:194px;height:293px;box-shadow:0 4px 0 rgba(255,255,255,.8)}
.col .head{height:59px;background:var(--white);border-radius:8px 8px 0 0;font-family:'Cinzel',serif;font-weight:700;color:var(--blue);font-size:21px;display:flex;align-items:center;justify-content:center}
.col ul{list-style:none;background:var(--blue-row);height:234px;padding-top:9px;border-radius:0 0 4px 4px}
.col li{height:42px;display:flex;align-items:center;justify-content:center;color:var(--white);font-size:14px;border-bottom:1px solid rgba(255,255,255,.25)}
.col li:last-child{border-bottom:none}
.col.features li{justify-content:flex-start;padding-left:22px}
.col.ours{top:111px;width:220px;height:326px;box-shadow:0 4px 16px rgba(0,0,0,.3);border-radius:8px;overflow:hidden}
.col.ours .head{height:78px;background:var(--ink);border-radius:0;color:var(--white);font-size:17px;gap:10px;line-height:20px;text-align:left}
.col.ours .head i{width:34px;height:34px;border-radius:50%;background:var(--white);display:block}
.col.ours ul{background:var(--white);height:248px;padding-top:6px}
.col.ours li{color:var(--ink);border-bottom:1px solid #ddd;margin:0 14px}

/* testimonials */
.testimonials{position:absolute;left:0;top:2853px;width:1200px;height:399px;background:var(--white)}
.testimonials h2{position:absolute;left:142px;top:70px}
.testimonials .quote{position:absolute;left:142px;top:120px}
.testimonials .text{position:absolute;left:142px;top:180px;width:440px;font-size:14.5px;line-height:24px;color:#555}
.testimonials .who{position:absolute;left:142px;top:262px;font-weight:700;color:var(--ink);font-size:15px}
.dots{position:absolute;left:142px;top:304px;display:flex;gap:8px}
.dots i{display:block;width:38px;height:4px;background:#cfe9f2}
.dots i:first-child{background:var(--blue)}
.portrait{position:absolute;left:640px;top:24px;width:380px;height:375px;background:linear-gradient(180deg,#f3f3f3 0%,#d9cfe0 40%,#5c3c72 75%,#2a2a2a 100%)}

/* footer */
.footer{position:absolute;left:0;top:3252px;width:1200px;height:225px;background:var(--foot-bg);text-align:center}
.badges{position:absolute;left:340px;top:42px;width:520px;display:flex;justify-content:space-between}
.badge{display:flex;flex-direction:column;align-items:center;gap:4px;width:150px}
.badge b{font-family:'Lato',sans-serif;font-weight:700;font-size:24px;color:#444}
.badge .stars{display:flex;gap:3px}
.links{position:absolute;left:140px;top:138px;width:920px;font-size:14px;color:#444;line-height:26px}
.links span{margin:0 8px}
.copyright{position:absolute;left:0;top:3477px;width:1200px;height:66px;background:var(--blue);color:var(--white);font-size:14px;display:flex;align-items:center;justify-content:center}
</style>
</head>
<body>

<div class="topbar">
  <div class="info" style="left:80px">
    <svg width="18" height="18" viewBox="0 0 18 18" fill="none" stroke="#fff" stroke-width="1.6"><circle cx="9" cy="9" r="7.5"/><path d="M9 4.5V9l3 2"/></svg>
    Mon-Fri 9:15am-5:30pm Sat 10am-2pm
  </div>
  <div class="info" style="left:404px">
    <svg width="18" height="18" viewBox="0 0 18 18" fill="none" stroke="#fff" stroke-width="1.6"><rect x="2" y="3.5" width="14" height="12" rx="1"/><path d="M2 7.5h14M6 2v3M12 2v3"/></svg>
    Book Appointments: Mon-Fri 8:30 am-5pm
  </div>
  <div class="social"><span>fk</span><span>cl</span><span>PG</span></div>
  <div class="book">BOOK APPOINTMENT</div>
</div>

<div class="header">
  <div class="brand">
    <div class="dot"></div>
    <div class="name">Bright Harbor<br>Smile Studio</div>
  </div>
  <div class="hinfo" style="left:555px">
    <div class="ic"><span><svg width="16" height="16" viewBox="0 0 16 16" fill="none" stroke="#fff" stroke-width="1.8"><path d="M11 4.5C10 3.5 8.8 3.2 8 3.2 6.3 3.2 5 4.1 5 5.5c0 3 6 1.8 6 5 0 1.4-1.4 2.3-3 2.3-1.2 0-2.4-.5-3.2-1.4M8 1.5v13"/></svg></span></div>
    <div>Click Here To Get Our $99<br>Teeth Whiting Deal (Reg: $378)</div>
  </div>
  <div class="hinfo" style="left:852px">
    <div class="ic"><span><svg width="14" height="18" viewBox="0 0 14 18" fill="#fff"><path d="M7 0C3.1 0 0 3 0 6.8 0 11.5 7 18 7 18s7-6.5 7-11.2C14 3 10.9 0 7 0zm0 9.5A2.7 2.7 0 1 1 7 4a2.7 2.7 0 0 1 0 5.5z"/></svg></span></div>
    <div>4410 Harbor View Rd. #112<br>Bayport, CA 90417</div>
  </div>
</div>

<nav class="nav">
  <ul>
    <li class="active">Home</li><li>Our Process</li><li>Photos</li><li>Free Treatment</li><li>Testimonials</li><li>Blog</li><li>FAQ</li><li>Contact</li><li>Gift Certificates</li>
  </ul>
  <div class="call"><svg width="22" height="22" viewBox="0 0 24 24" fill="#fff"><path d="M6.6 10.8a15.1 15.1 0 0 0 6.6 6.6l2.2-2.2c.3-.3.7-.4 1-.2 1.1.4 2.3.6 3.6.6.6 0 1 .4 1 1V20c0 .6-.4 1-1 1A17 17 0 0 1 3 4c0-.6.4-1 1-1h3.5c.6 0 1 .4 1 1 0 1.3.2 2.5.6 3.6.1.3 0 .7-.2 1z"/></svg></div>
</nav>

<section class="hero">
  <h1>GET THAT WHITE SMILE<br>YOU'VE ALWAYS WANTED</h1>
  <p>Amazing Results, The Most Effective System, More Affordable Than The Dentist</p>
  <div class="btn solid" style="left:78px;top:305px;width:196px">BOOK ONLINE</div>
  <div class="btn ghost" style="left:286px;top:305px;width:198px">CONTACT US</div>

  <div class="tile" role="img" aria-label="Happy customers holding a studio sign" style="left:590px;top:0"></div>
  <div class="tile" role="img" aria-label="Customer smiling after whitening" style="left:725px;top:0"></div>
  <div class="tile" role="img" aria-label="Customers with staff after treatment" style="left:858px;top:0"></div>
  <div class="tile" role="img" aria-label="Customer holding a review sign" style="left:992px;top:0"></div>
  <div class="tile" role="img" aria-label="Group of customers with staff" style="left:725px;top:125px"></div>
  <div class="tile" role="img" aria-label="Customer showing whitened smile" style="left:858px;top:125px"></div>
  <div class="tile" role="img" aria-label="Staff with a happy customer" style="left:590px;top:248px"></div>
  <div class="tile" role="img" aria-label="Customers holding a studio sign" style="left:858px;top:248px"></div>
  <div class="tile" role="img" aria-label="Customer with a best patient sign" style="left:992px;top:248px"></div>
  <div class="tile" role="img" aria-label="Staff members posing with customer" style="left:456px;top:371px"></div>
  <div class="tile" role="img" aria-label="Customer posing with a sign" style="left:725px;top:371px"></div>
</section>

<section class="about">
  <div class="video-frame"></div>
  <div class="video" role="img" aria-label="Studio introduction video">
    <div class="bar"></div>
  </div>
  <h2>BRIGHT HARBOR SMILE STUDIO</h2>
  <div class="lead">The best price, service and results.</div>
  <div class="body">Bright Harbor Smile Studio features state-of-the-art technologies that are safe, industry-unique and very cost-effective. Our teeth whitening system utilizes the latest blue light whitening technology. Our Blue Light Systems are calibrated precisely for optimal activation of our exclusive hydrogen peroxide based whitening solution which is manufactured in a FDA registered facility in the USA.</div>
</section>

<section class="how">
  <h2 class="section-title">HOW IT WORKS</h2>
  <div class="copy">
    <p>We have a very effective teeth whitening treatment that is guaranteed to get you quick results in about 1 hour. To start the treatment you'll apply a Hydrogen Peroxide based whitening agent to your teeth. We then place our cold blue light directly in front of your exposed teeth for 15 minutes per treatment. The lighting systems we use activate the whitening agent and thats what accelerates the whitening process, giving you whiter teeth in less than an hour.</p>
    <p>We always perform what we call a "Triple Treatment". So that's 3 of the 15 minute treatments all done consecutively, in the same visit. The actual whitening time is a total of 45 minutes. Now there is a few minute break in between each 15 minute treatment and this is why we tell all of our patients to give yourself one hour at the office. The biggest benefit of doing an in office treatment vs a take home kit is that you will see results immediately after the treatment. We also include our home maintenance kit for after care. It's very important that no matter where you get your teeth whitened, you need to maintain them for long lasting results. You'll use our maintenance kit once or twice per month as a touch up to help maintain your newly whitened teeth, and that ultimately make your results last longer.</p>
  </div>
</section>

<section class="why">
  <h2 class="section-title">WHY CHOOSE US</h2>

  <div class="card" style="left:208px;top:116px">
    <svg width="72" height="72" viewBox="0 0 72 72" fill="none" stroke="#0b9bc7" stroke-width="2.4"><path d="M38 6h26v26L32 64 6 38z"/><circle cx="52" cy="18" r="4"/><path d="M40 30c-2-2-5-2-7 0s-1 4 1 5 4 3 2 5-5 2-7 0M36 26l-2-2M30 44l2 2"/></svg>
    <span>Price</span>
  </div>
  <div class="card featured" style="left:480px;top:116px">
    <svg width="72" height="72" viewBox="0 0 72 72" fill="none" stroke="#fff" stroke-width="2.4"><path d="M6 10h60M10 10v36h52V10M36 46v8M26 64l10-10 10 10"/><path d="M22 38V30M32 38V24M42 38V28M52 38V20"/><circle cx="36" cy="6" r="3"/></svg>
    <span>Results</span>
  </div>
  <div class="card" style="left:751px;top:116px">
    <svg width="72" height="72" viewBox="0 0 72 72" fill="none" stroke="#0b9bc7" stroke-width="2.4"><circle cx="36" cy="36" r="30"/><circle cx="36" cy="36" r="23"/><path d="M20 20l32 32"/></svg>
    <span>No Pain</span>
  </div>
  <div class="card" style="left:208px;top:397px">
    <svg width="72" height="72" viewBox="0 0 72 72" fill="none" stroke="#0b9bc7" stroke-width="2.4"><circle cx="24" cy="24" r="9"/><path d="M24 6v6M24 36v6M6 24h6M36 24h6M11 11l4 4M33 33l4 4M11 37l4-4M37 11l-4 4"/><path d="M40 34c4-3 10-3 14 0 4-3 12-1 12 7 0 6-3 10-4 18-1 5-5 5-6 0l-2-8c-1-3-4-3-5 0l-2 8c-1 5-5 5-6 0-1-8-4-12-4-18 0-3 1-5 3-7z"/></svg>
    <span>Services</span>
  </div>
  <div class="card" style="left:480px;top:397px">
    <svg width="72" height="72" viewBox="0 0 72 72" fill="none" stroke="#0b9bc7" stroke-width="2.4"><path d="M8 66L50 18"/><path d="M48 20l6-6 10 10-6 6z"/><path d="M52 14l-3-5M57 12l-2-5M62 14l1-5M64 20l5-1"/></svg>
    <span>Convenience</span>
  </div>
  <div class="card" style="left:751px;top:397px">
    <svg width="72" height="72" viewBox="0 0 72 72" fill="none" stroke="#0b9bc7" stroke-width="2.4"><path d="M38 6h26v26L32 64 6 38z"/><circle cx="52" cy="18" r="4"/><path d="M40 30c-2-2-5-2-7 0s-1 4 1 5 4 3 2 5-5 2-7 0M36 26l-2-2M30 44l2 2"/></svg>
    <span>Price</span>
  </div>
</section>

<section class="compare">
  <h2 class="section-title" style="color:#fff">COMPARE US</h2>
  <div class="col features" style="left:78px">
    <div class="head">FEATURES</div>
    <ul><li>Speed</li><li>Ease of Use</li><li>Cost</li><li>Availability</li><li>Pain</li></ul>
  </div>
  <div class="col" style="left:288px">
    <div class="head">GLOWPRO</div>
    <ul><li>1-2 Hours</li><li>Difficult / Dentist</li><li>$300 - $600</li><li>Limited Availability</li><li>Pain &amp; Sensitivity</li></ul>
  </div>
  <div class="col ours" style="left:491px">
    <div class="head"><i></i><span>Bright Harbor<br>Smile Studio</span></div>
    <ul><li>45 Mins</li><li>Very Easy</li><li>$378</li><li>Appt Only</li><li style="border-bottom:none">No Pain</li></ul>
  </div>
  <div class="col" style="left:713px">
    <div class="head">SHINEWAVE</div>
    <ul><li>7-14 Days</li><li>Difficult / Dentist</li><li>$300 - $600</li><li>Limited Availability</li><li>Sensitivity</li></ul>
  </div>
  <div class="col" style="left:921px;width:201px">
    <div class="head">HOME KITS</div>
    <ul><li>7-30 Days</li><li>Difficult</li><li>$50 - $150</li><li>Store Purchase</li><li>Sensitivity</li></ul>
  </div>
</section>

<section class="testimonials">
  <h2 class="section-title">TESTIMONIALS</h2>
  <svg class="quote" width="44" height="34" viewBox="0 0 44 34" fill="#2e2e2e"><path d="M0 34V18C0 8 5 2 16 0l2 5c-6 2-8 5-8 11h8v18zM24 34V18c0-10 5-16 16-18l2 5c-6 2-8 5-8 11h8v18z"/></svg>
  <p class="text">Lorem Ipsum is simply dummy text of the printing and typesetting industry. Lorem Ipsum has been the industry's standard dummy text ever since the 1500s, when an unknown printer took a galley.</p>
  <div class="who">- NAME SURNAME</div>
  <div class="dots"><i></i><i></i><i></i></div>
  <div class="portrait" role="img" aria-label="Two staff members holding a best patient ever sign"></div>
</section>

<footer class="footer">
  <div class="badges">
    <div class="badge"><b>rateway</b><div class="stars">
      <svg width="80" height="14" viewBox="0 0 80 14" fill="#d32323"><path id="star" d="M7 0l2 5h5l-4 3 1.6 5L7 10l-4.6 3L4 8 0 5h5z"/><use href="#star" x="16"/><use href="#star" x="32"/><use href="#star" x="48"/><use href="#star" x="64"/></svg></div></div>
    <div class="badge"><b>friendbook</b><div class="stars">
      <svg width="80" height="14" viewBox="0 0 80 14" fill="#f5a623"><use href="#star"/><use href="#star" x="16"/><use href="#star" x="32"/><use href="#star" x="48"/><use href="#star" x="64"/></svg></div></div>
    <div class="badge"><b>searchly</b><div class="stars">
      <svg width="80" height="14" viewBox="0 0 80 14" fill="#f5a623"><use href="#star"/><use href="#star" x="16"/><use href="#star" x="32"/><use href="#star" x="48"/><use href="#star" x="64"/></svg></div></div>
  </div>
  <div class="links">
    <span>Home</span><span>Book Appointment Online</span><span>Our Process</span><span>Photos</span><span>Testimonials</span><span>Blog</span><span>FAQ</span><span>Contact</span><span>Gift Certificates</span><span>After Care</span><br>
    <span>Consent Form Espanol</span><span>Consent Form English</span><span>Cancellation Policy</span><span>Privacy Policy</span><span>Free Treatments</span>
  </div>
</footer>
<div class="copyright">2018 ©BRIGHT HARBOR SMILE STUDIO - All Rights Reserved</div>

</body>
</html>
```